Business card design and logo needed please help

I need a card for a new plumbing business. i want double sided gloss and on the front i need an attractive logo for my business the incorperates a rhino and plumbing to go with my name aswell as my contact info. logo aswell has to be not out there but remeberable as it will be representing this later to be large Business.Could also incorperate the initials of my buisness being VQB. On the back i want the type of work that i undertake, Plumbing, Maintaince, gasfitting and certification, sanitary drainage and stormwater, drain cleaning, All hot water systems installations and repair , FREE QUOTE is needed to stand out aswell. i like an indate colour design but more then one colour like black and grey or anything.info has to be easy to read that will draw in all types of clients. want a slogan on it saying "tough on Quality" aswell. Email aswell has changed to make it easier for people. Its now( Tlcadvisory@fernmail.test)
Industry/Entity Type
Business
Contact Information for Business Card
Borlo's Plumbing and Gas Fitting, Dale Marchetti, QBSA No. 48 07 316, ABN No. 74 205 913 480, Email. Borlosplumbingandgasfitting@fernmail.test, Mobile no. 0491 630 578
Logo styles of interest
Pictorial/Combination Logo
Abstract Logo
Character Logo
Look and feel

```html
<!DOCTYPE html>
<html lang="en">
<head>
<meta charset="utf-8">
<title>VQB Plumbing Services Card</title>
<link rel="stylesheet" href="https://fonts.googleapis.com/css2?family=Open+Sans:wght@400;700;800&display=swap">
<style>
  :root {
    --paper: #ffffff;
    --mint: #afe6de;
    --teal: #3aa8c9;
    --teal-deep: #2a8fb0;
    --ink: #111417;
    --shade: rgba(0, 0, 0, 0.28);
  }
  html, body {
    margin: 0;
    padding: 0;
    overflow: hidden;
    background: var(--paper);
  }
  .card {
    position: relative;
    width: 1200px;
    height: 679px;
    overflow: hidden;
    background: var(--paper);
    font-family: "Open Sans", Arial, sans-serif;
  }
  .wave {
    position: absolute;
    inset: 0;
  }
  .quote-call {
    position: absolute;
    top: 10px;
    left: 0;
    width: 1200px;
    margin: 0;
    text-align: center;
    font-weight: 800;
    font-size: 44px;
    letter-spacing: 0.5px;
    color: var(--teal);
    -webkit-text-stroke: 1px var(--teal-deep);
    text-shadow: 0 2px 3px var(--shade);
  }
  .brand-name {
    position: absolute;
    left: 40px;
    top: 300px;
    margin: 0;
    font-weight: 700;
    font-size: 205px;
    line-height: 1;
    letter-spacing: 4px;
    color: var(--teal);
  }
  .services {
    position: absolute;
    right: 34px;
    top: 150px;
    margin: 0;
    padding: 0;
    list-style: none;
    text-align: right;
    font-size: 44px;
    line-height: 62.8px;
    color: var(--ink);
  }
  .services b {
    font-weight: 700;
  }
</style>
</head>
<body>
  <div class="card">
    <svg class="wave" width="1200" height="679" viewBox="0 0 1200 679" aria-hidden="true">
      <defs>
        <filter id="edge-shadow" x="-5%" y="-5%" width="110%" height="120%">
          <feDropShadow dx="0" dy="4" stdDeviation="5" flood-color="#000" flood-opacity="0.3"/>
        </filter>
      </defs>
      <path d="M0,505 C320,515 470,495 575,345 C690,180 860,30 1200,0 L1200,679 L0,679 Z"
            fill="var(--mint)" filter="url(#edge-shadow)"/>
      <path d="M0,505 C320,515 470,495 575,345 C690,180 860,30 1200,0"
            fill="none" stroke="var(--teal)" stroke-width="5"/>
    </svg>

    <p class="quote-call">CALL FOR FREE QUOTE</p>

    <p class="brand-name">VQB</p>

    <ul class="services">
      <li><b>P</b>lumbing</li>
      <li>installations</li>
      <li>&amp; maintenance</li>
      <li><b>S</b>tormwater &amp; tanks</li>
      <li><b>D</b>rain cleaning services</li>
      <li><b>S</b>anitary drainage &amp; repairs</li>
      <li><b>H</b>ot water system Installations &amp; repairs</li>
      <li><b>G</b>as fitting Installation, repairs and Certification</li>
    </ul>
  </div>
</body>
</html>
```